Stationery Design Project

Hi All,

We need you to design stationary for a new Business and Accounting Advisory Firm. We have already got the logo designed and it is attached. If you could also if possible, match the fonts in your design to that on the logo’s provided.

What we need:
- Business Card
- A4 Letter head
- A4 Folders
- PPT template (Title page and regular page)

And what ever else you want to throw in.

We are in the process of getting the web site designed, however below is a list of websites which we like which will give you an understanding of the style that we are going for.

- plivant.example
- moldrabay.example
- tarvenhook.example
- quillorbank.example

I look forward to your seeing your design.
Updates

Hi All,

I have just realised that I forgot that i need to include a Sworn Ledgerkeepers image on the letter head, please find attaced as File 1. Could you please have this image in the bottom left header.

Regards,

Marcus

Industry/Entity Type

Business

Requirements
Must have
• Outputs:
- Documents ready to print
- Generic editable information
- Pdf copies of the documents
- Word version of letterhead

```html
<!DOCTYPE html>
<html lang="en">
<head>
<meta charset="utf-8">
<title>Corvell Partners – Stationery Suite</title>
<link href="https://fonts.googleapis.com/css2?family=Crimson+Pro:wght@400&family=Open+Sans:wght@400;700;800&family=PT+Sans:wght@400&display=swap" rel="stylesheet">
<style>
  :root{
    --bg:#a6a8ab;
    --paper:#ffffff;
    --paper-shade:#eeeeee;
    --blue:#2a7fc1;
    --navy:#3a4a9a;
    --teal:#22b6c8;
    --orange:#f7941d;
    --orange-deep:#f26a21;
    --ink:#2f2f2f;
    --muted:#8a8a8a;
    --rule:#9a9a9a;
    --badge:#c4262e;
    --label:#ffffff;
  }
  *{box-sizing:border-box;margin:0;padding:0}
  html,body{width:1200px;height:420px;overflow:hidden;background:var(--bg)}
  .canvas{position:relative;width:1200px;height:420px;overflow:hidden;background:var(--bg);font-family:'Open Sans',sans-serif;color:var(--ink)}
  .abs{position:absolute}

  /* shared parts */
  .sheet{position:absolute;background:linear-gradient(160deg,var(--paper) 40%,var(--paper-shade));box-shadow:0 1px 3px rgba(0,0,0,.25);overflow:hidden}
  .brand-bar{position:absolute;left:0;right:0;bottom:0;height:3px;background:linear-gradient(90deg,var(--navy),var(--blue) 55%,var(--teal))}
  .fine{font-family:'PT Sans',sans-serif;font-size:3.4px;color:var(--muted);white-space:nowrap;line-height:1.3}
  .web{font-family:'Crimson Pro',serif;font-size:5px;color:var(--ink);letter-spacing:.04em;white-space:nowrap}
  .label{position:absolute;font-family:'PT Sans',sans-serif;font-size:15px;color:var(--label);white-space:nowrap}

  .logo{display:flex;align-items:center;gap:.35em;line-height:1;white-space:nowrap}
  .logo-dot{width:1.5em;height:1.5em;border-radius:50%;background:var(--orange);flex:none}
  .logo-text{display:flex;flex-direction:column}
  .logo-name{font-family:'Crimson Pro',serif;font-weight:400;color:var(--blue);font-size:1em}
  .logo-tag{font-family:'PT Sans',sans-serif;font-size:.42em;letter-spacing:.28em;color:var(--muted);margin-top:.2em}
  .logo--white .logo-name{color:var(--paper)}
  .logo--white .logo-dot{background:var(--paper)}

  .ghost-mark{position:absolute;border-radius:50%;background:radial-gradient(circle,rgba(42,127,193,.10),rgba(247,148,29,.08));}
  .badge{position:absolute;border-radius:50%;background:var(--badge)}

  /* folder */
  .folder-panel{top:10px;width:158px;height:204px}
  .pocket{position:absolute;top:214px;height:43px;display:flex;align-items:center;justify-content:center}
  .pocket--left{left:12px;width:158px;background:var(--paper);clip-path:polygon(0 0,100% 0,90% 100%,0 100%)}
  .pocket--right{left:170px;width:158px;background:linear-gradient(90deg,var(--orange-deep),var(--orange));clip-path:polygon(10% 0,100% 0,100% 100%,0 100%)}

  /* fax */
  .fax-title{font-size:11px;font-weight:400;letter-spacing:.02em}
  .fax-fields{display:grid;grid-template-columns:1fr 1fr;column-gap:10px;row-gap:3px;width:138px}
  .fax-field{font-size:3.4px;color:var(--ink);border-bottom:.5px solid var(--rule);padding-bottom:1px}
  .fax-checks{display:flex;gap:6px}
  .fax-check{display:flex;align-items:center;gap:1.5px;font-size:3.2px;white-space:nowrap}
  .fax-check::before{content:"";width:3px;height:3px;border:.5px solid var(--ink)}

  /* envelopes */
  .env-flap{position:absolute;left:0;top:0;width:100%;height:30px;background:linear-gradient(90deg,var(--orange-deep),var(--orange));clip-path:polygon(0 0,100% 0,100% 55%,50% 100%,0 55%);display:flex;justify-content:center;padding-top:6px}

  /* business cards */
  .card{position:absolute;top:199px;height:45px;box-shadow:0 1px 2px rgba(0,0,0,.25);overflow:hidden}
  .card--white{background:var(--paper)}
  .card--orange{background:linear-gradient(135deg,var(--orange),var(--orange-deep));display:flex;align-items:center;justify-content:center}
  .card-name{font-size:4.2px;font-weight:700}
  .card-role{font-size:3.2px;color:var(--muted)}

  /* slides */
  .slide{top:267px;width:161px;height:121px}
  .slide-heading{position:absolute;top:8px;font-size:8px;font-weight:800;color:var(--ink);letter-spacing:.01em}
  .slide-body{font-size:3.5px;color:var(--muted);line-height:1.35}
  .bullets{list-style:none;display:flex;flex-direction:column;gap:6px}
  .bullets li{font-size:3.4px;color:var(--ink);display:flex;align-items:center;gap:3px;white-space:nowrap}
  .bullets li::before{content:"";width:2.5px;height:2.5px;border-radius:50%;background:var(--badge);flex:none}
  .subtitle{font-size:3.6px;font-weight:700;color:var(--ink)}
  .subtitle::before{content:"";display:inline-block;width:2.5px;height:2.5px;border-radius:50%;background:var(--badge);margin-right:2px;vertical-align:middle}
  .photo{position:absolute;top:48px;width:72px;height:52px}
  .flow-head{position:absolute;width:27px;height:8px;border-radius:1px;background:linear-gradient(var(--blue),var(--navy));font-size:2.6px;color:var(--paper);display:flex;align-items:center;justify-content:center}
  .flow-box{position:absolute;width:21px;height:11px;border-radius:3px/2px;background:linear-gradient(var(--orange),var(--orange-deep));font-size:2.4px;color:var(--paper);display:flex;align-items:center;justify-content:center}
  .thanks{font-size:11px;font-weight:800;color:var(--blue)}
</style>
</head>
<body>
<main class="canvas">

  <!-- Folder -->
  <section class="sheet folder-panel" style="left:12px">
    <div class="ghost-mark" style="left:26px;top:52px;width:78px;height:78px"></div>
    <div class="logo abs" style="left:40px;top:188px;font-size:9px">
      <span class="logo-dot"></span>
      <span class="logo-text"><span class="logo-name">Corvell Partners</span><span class="logo-tag">BUSINESS ADVISORS</span></span>
    </div>
    <p class="fine abs" style="left:52px;top:203px">12 Harbour Lane, Easton NS 2040</p>
    <p class="fine abs" style="left:30px;top:208px">T 02 5550 1842 · E hello@corvellpartners.example</p>
    <span class="brand-bar"></span>
  </section>
  <section class="sheet folder-panel" style="left:170px">
    <div class="logo abs" style="left:28px;top:62px;font-size:12px">
      <span class="logo-dot"></span>
      <span class="logo-text"><span class="logo-name">Corvell Partners</span><span class="logo-tag">BUSINESS ADVISORS</span></span>
    </div>
    <p class="web abs" style="right:10px;top:193px">www.corvellpartners.example</p>
    <span class="brand-bar"></span>
  </section>
  <div class="pocket pocket--left">
    <div class="logo" style="font-size:10px"><span class="logo-dot"></span><span class="logo-name">Corvell</span></div>
  </div>
  <div class="pocket pocket--right">
    <div class="logo logo--white" style="font-size:12px"><span class="logo-dot"></span><span class="logo-name">Corvell</span></div>
  </div>
  <p class="label" style="left:64px;top:262px">Folder</p>

  <!-- Letterhead option 1 -->
  <section class="sheet" style="left:339px;top:24px;width:159px;height:205px">
    <div class="logo abs" style="left:42px;top:8px;font-size:8px">
      <span class="logo-dot"></span>
      <span class="logo-text"><span class="logo-name">Corvell Partners</span><span class="logo-tag">BUSINESS ADVISORS</span></span>
    </div>
    <div class="ghost-mark" style="left:42px;top:80px;width:74px;height:74px"></div>
    <span class="badge" style="left:6px;top:178px;width:21px;height:21px"></span>
    <p class="fine abs" style="left:56px;top:186px">12 Harbour Lane, Easton NS 2040</p>
    <p class="fine abs" style="left:38px;top:191px">T 02 5550 1842 · E hello@corvellpartners.example</p>
    <span class="brand-bar"></span>
  </section>
  <p class="label" style="left:394px;top:234px">Option-1</p>

  <!-- Letterhead option 2 -->
  <section class="sheet" style="left:514px;top:24px;width:159px;height:205px">
    <div class="logo abs" style="left:6px;top:8px;font-size:8px">
      <span class="logo-dot"></span>
      <span class="logo-text"><span class="logo-name">Corvell Partners</span><span class="logo-tag">BUSINESS ADVISORS</span></span>
    </div>
    <p class="fine abs" style="left:104px;top:11px">12 Harbour Lane,<br>Easton NS 2040</p>
    <span class="badge" style="left:6px;top:185px;width:13px;height:13px"></span>
    <p class="abs" style="left:21px;top:186px;font-size:4.4px;font-weight:700;line-height:1.1">Sworn<br>Ledgerkeepers</p>
    <p class="fine abs" style="left:76px;top:192px">T 02 5550 1842 · E hello@corvell.example</p>
    <span class="brand-bar"></span>
  </section>
  <p class="label" style="left:566px;top:234px">Option-2</p>

  <!-- Letterhead option 3: fax -->
  <section class="sheet" style="left:689px;top:24px;width:158px;height:205px">
    <div class="logo abs" style="left:42px;top:8px;font-size:8px">
      <span class="logo-dot"></span>
      <span class="logo-text"><span class="logo-name">Corvell Partners</span><span class="logo-tag">BUSINESS ADVISORS</span></span>
    </div>
    <h2 class="fax-title abs" style="left:10px;top:46px">FAX</h2>
    <div class="fax-fields abs" style="left:10px;top:64px">
      <span class="fax-field">To :</span><span class="fax-field">From :</span>
      <span class="fax-field">Fax :</span><span class="fax-field">Pages :</span>
      <span class="fax-field">Phone :</span><span class="fax-field">Date :</span>
      <span class="fax-field">Re :</span><span class="fax-field">CC :</span>
    </div>
    <div class="fax-checks abs" style="left:10px;top:104px">
      <span class="fax-check">Urgent</span><span class="fax-check">For Review</span><span class="fax-check">Please Comment</span><span class="fax-check">Please Reply</span><span class="fax-check">Please Recycle</span>
    </div>
    <p class="fine abs" style="left:56px;top:186px">12 Harbour Lane, Easton NS 2040</p>
    <p class="fine abs" style="left:38px;top:191px">T 02 5550 1842 · E hello@corvellpartners.example</p>
    <span class="brand-bar"></span>
  </section>
  <p class="label" style="left:740px;top:234px">Option-3</p>

  <!-- Envelopes -->
  <section class="sheet" style="left:947px;top:32px;width:177px;height:78px">
    <div class="env-flap">
      <div class="logo logo--white" style="font-size:9px"><span class="logo-dot"></span><span class="logo-name">Corvell</span></div>
    </div>
  </section>
  <section class="sheet" style="left:908px;top:66px;width:190px;height:114px">
    <svg class="abs" style="left:0;top:0" width="190" height="40" viewBox="0 0 190 40" aria-hidden="true">
      <polyline points="0,0 95,30 190,0" fill="none" stroke="#9a9a9a" stroke-width=".6"/>
    </svg>
    <div class="logo abs" style="left:80px;top:12px;font-size:7px"><span class="logo-dot"></span><span class="logo-name">Corvell</span></div>
    <div class="logo abs" style="left:24px;top:50px;font-size:8px">
      <span class="logo-dot"></span>
      <span class="logo-text"><span class="logo-name">Corvell Partners</span><span class="logo-tag">BUSINESS ADVISORS</span></span>
    </div>
    <p class="fine abs" style="left:24px;top:66px">12 Harbour Lane, Easton NS 2040</p>
    <p class="web abs" style="left:24px;top:102px">www.corvellpartners.example</p>
    <span class="brand-bar"></span>
  </section>

  <!-- Business cards -->
  <section class="card card--white" style="left:853px;width:82px">
    <div class="logo abs" style="left:4px;top:6px;font-size:5.5px">
      <span class="logo-dot"></span>
      <span class="logo-text"><span class="logo-name">Corvell Partners</span><span class="logo-tag">BUSINESS ADVISORS</span></span>
    </div>
    <p class="fine abs" style="left:20px;top:18px">T 02 5550 1842<br>E hello@corvell.example</p>
    <span class="brand-bar" style="height:2px"></span>
  </section>
  <p class="abs" style="left:874px;top:247px;font-size:4px;color:var(--label)">Email Signature</p>

  <section class="card card--white" style="left:942px;width:82px">
    <div class="logo abs" style="left:16px;top:5px;font-size:5.5px">
      <span class="logo-dot"></span>
      <span class="logo-text"><span class="logo-name">Corvell Partners</span><span class="logo-tag">BUSINESS ADVISORS</span></span>
    </div>
    <p class="abs" style="left:5px;top:19px"><span class="card-name">Your Name</span><br><span class="card-role">Designation</span></p>
    <p class="fine abs" style="left:42px;top:19px">T 02 5550 1842<br>M 0455 501 842<br>E hello@corvell.example</p>
    <span class="brand-bar" style="height:2px"></span>
  </section>

  <section class="card card--white" style="left:1027px;width:80px">
    <div class="logo abs" style="left:12px;top:15px;font-size:6px">
      <span class="logo-dot"></span>
      <span class="logo-text"><span class="logo-name">Corvell Partners</span><span class="logo-tag">BUSINESS ADVISORS</span></span>
    </div>
    <span class="brand-bar" style="height:2px"></span>
  </section>

  <section class="card card--orange" style="left:1111px;width:80px">
    <div class="logo logo--white" style="font-size:10px"><span class="logo-dot"></span><span class="logo-name">Corvell</span></div>
  </section>

  <!-- Presentation slides -->
  <section class="sheet slide" style="left:164px">
    <div class="logo abs" style="left:25px;top:28px;font-size:12px">
      <span class="logo-dot"></span>
      <span class="logo-text"><span class="logo-name">Corvell Partners</span><span class="logo-tag">BUSINESS ADVISORS</span></span>
    </div>
    <h1 class="abs" style="left:0;right:0;top:70px;text-align:center;font-size:8.5px;font-weight:700">TITLE OF PRESENTATION</h1>
    <p class="web abs" style="left:52px;top:107px">www.corvellpartners.example</p>
    <span class="brand-bar"></span>
  </section>

  <section class="sheet slide" style="left:332px">
    <h2 class="slide-heading" style="left:0;right:0;text-align:center">LOREM IPSUM</h2>
    <p class="slide-body abs" style="left:14px;right:14px;top:22px">Lorem ipsum dolor sit amet, consectetuer adipiscing elit, sed diam nonummy nibh euismod tincidunt ut laoreet dolore magna aliquam erat volutpat. Ut wisi enim ad minim veniam, quis nostrud exerci tation.</p>
    <div class="photo" style="left:8px;background:linear-gradient(135deg,#c9ced3,#5d6670)" role="img" aria-label="Photo of business partners shaking hands in an office lobby"></div>
    <div class="photo" style="left:82px;background:linear-gradient(135deg,#d8dadc,#6f757b)" role="img" aria-label="Photo of a hand reviewing financial paperwork with a pen"></div>
    <span class="brand-bar"></span>
  </section>

  <section class="sheet slide" style="left:506px">
    <h2 class="slide-heading" style="left:12px">LOREM IPSUM</h2>
    <div class="flow-head" style="left:14px;top:32px">Lorem ipsum</div>
    <div class="flow-head" style="left:47px;top:32px">Lorem ipsum</div>
    <div class="flow-head" style="left:80px;top:32px">Lorem ipsum</div>
    <div class="flow-head" style="left:113px;top:32px">Lorem ipsum</div>
    <div class="flow-box" style="left:17px;top:46px">Lorem</div><div class="flow-box" style="left:50px;top:46px">Lorem</div><div class="flow-box" style="left:83px;top:46px">Lorem</div><div class="flow-box" style="left:116px;top:46px">Lorem</div>
    <div class="flow-box" style="left:17px;top:63px">Lorem</div><div class="flow-box" style="left:50px;top:63px">Lorem</div><div class="flow-box" style="left:83px;top:63px">Lorem</div><div class="flow-box" style="left:116px;top:63px">Lorem</div>
    <div class="flow-box" style="left:17px;top:80px">Lorem</div><div class="flow-box" style="left:50px;top:80px">Lorem</div><div class="flow-box" style="left:83px;top:80px">Lorem</div><div class="flow-box" style="left:116px;top:80px">Lorem</div>
    <span class="brand-bar"></span>
  </section>

  <section class="sheet slide" style="left:678px">
    <h2 class="slide-heading" style="left:12px">LOREM IPSUM</h2>
    <ul class="bullets abs" style="left:14px;top:34px">
      <li>Lorem ipsum dolor sit amet, consectetuer adipiscing elit, sed diam nonummy.</li>
      <li>Lorem ipsum dolor sit amet, consectetuer adipiscing elit, sed diam nonummy.</li>
      <li>Lorem ipsum dolor sit amet, consectetuer adipiscing elit, sed diam nonummy.</li>
      <li>Lorem ipsum dolor sit amet, consectetuer adipiscing elit, sed diam nonummy.</li>
      <li>Lorem ipsum dolor sit amet, consectetuer adipiscing elit, sed diam nonummy.</li>
      <li>Lorem ipsum dolor sit amet, consectetuer.</li>
    </ul>
    <div class="logo abs" style="right:6px;top:101px;font-size:7px"><span class="logo-dot"></span><span class="logo-name">Corvell</span></div>
    <span class="brand-bar"></span>
  </section>

  <section class="sheet slide" style="left:850px">
    <h2 class="slide-heading" style="left:12px">LOREM IPSUM</h2>
    <div class="abs" style="left:16px;top:32px;width:60px;display:flex;flex-direction:column;gap:8px">
      <p><span class="subtitle">Sub Title 1</span><br><span class="slide-body">Lorem ipsum dolor sit amet, consectetuer adipiscing elit.</span></p>
      <p><span class="subtitle">Sub Title 2</span><br><span class="slide-body">Lorem ipsum dolor sit amet, consectetuer adipiscing elit.</span></p>
      <p><span class="subtitle">Sub Title 3</span><br><span class="slide-body">Lorem ipsum dolor sit amet, consectetuer adipiscing elit.</span></p>
    </div>
    <div class="abs" style="left:86px;top:32px;width:60px;display:flex;flex-direction:column;gap:8px">
      <p><span class="subtitle">Sub Title 1</span><br><span class="slide-body">Lorem ipsum dolor sit amet, consectetuer adipiscing elit.</span></p>
      <p><span class="subtitle">Sub Title 2</span><br><span class="slide-body">Lorem ipsum dolor sit amet, consectetuer adipiscing elit.</span></p>
      <p><span class="subtitle">Sub Title 3</span><br><span class="slide-body">Lorem ipsum dolor sit amet, consectetuer adipiscing elit.</span></p>
    </div>
    <div class="logo abs" style="right:6px;top:101px;font-size:7px"><span class="logo-dot"></span><span class="logo-name">Corvell</span></div>
    <span class="brand-bar"></span>
  </section>

  <section class="sheet slide" style="left:1018px">
    <div class="logo abs" style="left:30px;top:22px;font-size:11px">
      <span class="logo-dot"></span>
      <span class="logo-text"><span class="logo-name">Corvell Partners</span><span class="logo-tag">BUSINESS ADVISORS</span></span>
    </div>
    <p class="thanks abs" style="left:0;right:0;top:55px;text-align:center">Thank You!</p>
    <p class="abs" style="left:0;right:0;top:70px;text-align:center;font-size:6px;font-weight:700">For your attention</p>
    <p class="web abs" style="left:0;right:0;top:80px;text-align:center">www.corvellpartners.example</p>
  </section>

  <p class="label" style="left:474px;top:395px;font-size:17px">PowerPoint Presentation</p>
</main>
</body>
</html>
```